A specialised Sport management needs a corporate brochure design

We are a specialized company in the management and consultancy of sports events. and need to have a company brochure
We provide the following services;
Event management
Venues management
Production
Ticketing
Consulting
Hospitality
Activity management
Event timing
Branding of event
Event supplies
We need a corporate profile design for our company to showcase the major events that we have covered , with images, information, statistics, surveys, products and services used. We want to highlight our professionalism and execution of the events, experience of the participants, spectators . How we have grown in the past few years and reached the international standards.
Objectives of the work:
To get sponsors and partners for future business and to present Tri-Crest
as not just a sports management company but also a professional sports
events management company.
You can check our website
www.tri-crest.example
Target Market(s)
Sponsors and corporate partners
Industry/Entity Type
Events
Requirements
Must have
- Must Have:
- - Very professional look
- -Some event images,Event information, statistics, surveys, products and services used. We want to highlight our professionalism and execution of the events (Attached)
Nice to have
- Similar momentom of the below design
- http://www.lumavent.example/wp-content/themes/lumavent/pdf/CP-2014-15-V10-Web.pdf

```html
<!DOCTYPE html>
<html lang="en">
<head>
<meta charset="utf-8">
<title>Tri-Crest – Testimonials &amp; Contact</title>
<link rel="stylesheet" href="https://fonts.googleapis.com/css2?family=Bebas+Neue&family=Inter:wght@400;700&display=swap">
<style>
  :root {
    --backdrop: #000000;
    --sheet: #808080;
    --ink: #ffffff;
  }
  * { margin: 0; padding: 0; box-sizing: border-box; }
  html, body {
    width: 1200px; height: 1172px; overflow: hidden;
    background: var(--backdrop);
  }
  .sheet {
    position: absolute; left: 49px; top: 162px;
    width: 1091px; height: 849px;
    background: var(--sheet);
    color: var(--ink);
    font-family: "Inter", Helvetica, Arial, sans-serif;
  }
  .testimonial {
    position: absolute; left: 67px;
    white-space: nowrap;
  }
  .testimonial__quote {
    font-size: 17.5px; line-height: 24px; font-weight: 400;
    letter-spacing: -0.1px;
  }
  .testimonial__name {
    font-size: 17.5px; line-height: 24px; font-weight: 700;
    margin-top: 10px;
  }
  .testimonial__role {
    font-size: 17.5px; line-height: 22px; font-weight: 400;
  }
  .divider {
    position: absolute; left: 67px;
    width: 68px; height: 3px; background: var(--ink);
  }
  .contact {
    position: absolute; left: 818px; top: 658px;
    white-space: nowrap;
  }
  .contact__title {
    font-family: "Bebas Neue", "Oswald", sans-serif;
    font-size: 58px; line-height: 1; letter-spacing: 0.5px;
    font-weight: 400;
  }
  .contact__list {
    list-style: none; margin-top: 10px;
    font-size: 14px; line-height: 19px;
  }
</style>
</head>
<body>
  <main class="sheet">
    <section class="testimonial" style="top:46px">
      <p class="testimonial__quote">“Awesome people, awesome events, thank you for renewing<br>the hope of sports in Kuwait”</p>
      <p class="testimonial__name">Karim Nasseri</p>
    </section>
    <div class="divider" style="top:155px"></div>

    <section class="testimonial" style="top:185px">
      <p class="testimonial__quote">“Haven’t tried any Event managers before Tri-Crest,<br>don’t want to try any others”</p>
      <p class="testimonial__name">Fahad Almutawa</p>
      <p class="testimonial__role">Founder Lapline+</p>
    </section>
    <div class="divider" style="top:319px"></div>

    <section class="testimonial" style="top:350px">
      <p class="testimonial__quote">“To all who helped me and participated in the marathon<br>yesterday. Thank you for the experience. For people who<br>currently struggle and live with chronic disease like myself,<br>I proved to my self that if you are committed to your goals<br>and push thrugh you will win! I thank Tri-Crest for giving the<br>space for us to challenge our limits and ourselves! Change in<br>diet, lifestyle, and never giving up is key to success.”</p>
      <p class="testimonial__name">StrideWellKW</p>
    </section>
    <div class="divider" style="top:576px"></div>

    <section class="testimonial" style="top:606px">
      <p class="testimonial__quote">“CONGRATULATIONS on a great event last weekend!<br>In terms of events in Kuwait that I personally have entered<br>this was far by the stand out one. I was impressed by the<br>numbers of attendees from so many different nationalities<br>and abilities making it a truly global event within Kuwait.”</p>
      <p class="testimonial__name" style="margin-top:4px">Martin Haldane</p>
      <p class="testimonial__role">General Manager - Seafront Athletic Club</p>
    </section>

    <section class="contact">
      <h2 class="contact__title">Contact Us</h2>
      <ul class="contact__list">
        <li>Mob: 965 5550 1234</li>
        <li>Tel: 965 5550 9876</li>
        <li>Email: events@tri-crest.example</li>
        <li>Website: www.tri-crest.example</li>
      </ul>
    </section>
  </main>
</body>
</html>
```